Multi-Line Insurance PPC Landing Page - Conversion optimized.

We have a PPC landing page used for the general population to get an insurance quote through an agent's site.

We'd like to improve the page for PPC traffic, make it more conversion friendly.

Site should be a single long page.

We will dynamically change the form and headlines on the page depending on what insurance "line" is being called. ie, Lift, Auto, Home, Business.

The enclosed AI file has all of the raw elements we need. We're looking to enhance the design and conversion ability.

Target Market(s)

General public needed insurance services.

Industry/Entity Type

Insurance Broker

Number of Pages Required

1 page

Font styles to use
Sans Serif

Requirements
Must have
• Form, agent picture, name, address.

```html
<!DOCTYPE html>
<html lang="en">
<head>
<meta charset="utf-8">
<title>Harbor Quote – Get a Quote</title>
<link href="https://fonts.googleapis.com/css2?family=Cinzel:wght@400;700&family=Open+Sans:wght@400;600;700&display=swap" rel="stylesheet">
<style>
:root{
  --blue:#1c84c6;
  --blue-dark:#0f4f8a;
  --navy:#1d3f78;
  --ink:#333;
  --muted:#666;
  --gray:#ececec;
  --hex:#2b2b2b;
  --accent:#c0392b;
  --white:#fff;
}
*{box-sizing:border-box;margin:0;padding:0}
html,body{width:721px;height:1200px;overflow:hidden}
body{font-family:"Open Sans",Arial,sans-serif;color:var(--ink);background:var(--white);position:relative}
.header{height:42px;display:flex;align-items:center;justify-content:space-between;padding:0 28px}
.brand{display:flex;align-items:center;gap:8px;font-family:"Open Sans",Arial,sans-serif;font-weight:700;font-size:20px;color:var(--blue-dark)}
.brand i{display:block;width:14px;height:14px;background:var(--blue)}
.phone{display:flex;align-items:center;gap:6px;font-size:15px;color:var(--blue-dark);font-weight:600}
.hero{position:relative;height:250px;background:linear-gradient(180deg,#1f8fd4,#1876b8)}
.hero-art{position:absolute;left:410px;top:10px;width:245px;height:228px;border-radius:6px;background:radial-gradient(circle at 50% 40%,rgba(255,255,255,.55),rgba(255,255,255,.12) 70%)}
.hero-title{position:absolute;left:14px;top:96px;width:320px;color:var(--white);font-weight:700;font-size:15px;line-height:1.4}
.btn{display:inline-block;font-size:9px;font-weight:700;padding:5px 10px;border-radius:2px;text-transform:uppercase;letter-spacing:.3px}
.hero .btn{position:absolute;left:14px;top:150px;background:var(--white);color:var(--blue-dark)}
.quote-card{position:absolute;left:72px;top:290px;width:576px;height:205px;background:var(--white);box-shadow:0 2px 8px rgba(0,0,0,.25);display:flex}
.agent{width:190px;padding:12px 14px;text-align:center;border-right:1px solid #ddd}
.agent-photo{width:86px;height:96px;margin:0 auto 6px;background:linear-gradient(#c9ced6,#8e99a8);clip-path:polygon(50% 0,100% 25%,100% 75%,50% 100%,0 75%,0 25%)}
.agent-name{font-family:"Cinzel",Georgia,serif;color:var(--blue);font-size:12px;font-weight:700}
.agent p{font-size:8px;color:var(--muted);line-height:1.5}
.agent .contact{color:var(--blue-dark);font-weight:600}
.form{flex:1;padding:10px 18px}
.form h2{font-family:"Cinzel",Georgia,serif;color:var(--blue);font-size:15px;text-align:center;margin-bottom:8px}
.form h2 b{color:var(--ink)}
.fields{display:grid;grid-template-columns:1fr 1fr;gap:4px 14px}
.field label{display:block;font-size:7px;color:var(--muted)}
.field span{display:block;height:13px;border:1px solid #ccc;border-radius:2px;font-size:7px;color:#999;padding:1px 4px}
.submit{display:block;margin:8px 0 0 auto;width:80px;text-align:center;background:var(--navy);color:var(--white)}
.about{position:absolute;top:495px;left:0;width:721px;height:95px;background:var(--gray);text-align:center;padding:18px 40px 0;overflow:hidden}
h3{font-family:"Cinzel",Georgia,serif;color:var(--blue);font-size:16px;margin-bottom:6px}
h3 b{color:var(--ink)}
.about p{font-size:7px;color:var(--muted);line-height:1.45}
.products{position:absolute;top:590px;left:0;width:721px;height:275px;text-align:center;padding-top:30px}
.rule{width:160px;height:1px;background:#ccc;margin:4px auto 18px}
.grid{display:flex;justify-content:center;gap:38px}
.product{width:120px}
.hexicon{width:66px;height:72px;margin:0 auto 8px;background:var(--hex);clip-path:polygon(50% 0,100% 25%,100% 75%,50% 100%,0 75%,0 25%);display:flex;align-items:center;justify-content:center}
.product h4{font-family:"Cinzel",Georgia,serif;color:var(--blue);font-size:13px;margin-bottom:4px}
.product p{font-size:7px;color:var(--muted);line-height:1.45;margin-bottom:6px}
.product .btn{background:var(--navy);color:var(--white)}
.testimonials{position:absolute;top:865px;left:0;width:721px;height:250px;background:var(--gray);text-align:center;padding-top:22px}
.faces{display:flex;justify-content:center;align-items:center;gap:110px}
.face{background:linear-gradient(#cfd4da,#9aa4b1);clip-path:polygon(50% 0,100% 25%,100% 75%,50% 100%,0 75%,0 25%)}
.face.side{width:70px;height:80px}
.face.main{width:100px;height:112px;background:linear-gradient(#b9dd9a,#6fa84f)}
.arrow{position:absolute;top:115px}
.t-name{font-family:"Cinzel",Georgia,serif;color:var(--accent);font-size:10px;font-weight:700;margin-top:6px}
.testimonials p{font-size:7px;color:var(--muted);line-height:1.45}
.footer{position:absolute;top:1115px;left:0;width:721px;height:85px;background:var(--blue-dark);color:#dbe8f5;text-align:center;padding:10px 50px}
.footer h5{font-size:8px;font-weight:700;color:var(--white);margin-bottom:3px}
.footer p{font-size:7px;line-height:1.5}
.footer .copy{margin-top:8px}
</style>
</head>
<body>
<header class="header">
  <div class="brand"><i></i>Harbor Quote</div>
  <div class="phone">
    <svg width="16" height="16" viewBox="0 0 24 24"><circle cx="12" cy="12" r="11" fill="none" stroke="#0f4f8a" stroke-width="2"/><path d="M8 6l2 0 1 3-1.5 1a7 7 0 0 0 4 4l1-1.5 3 1v2a1.5 1.5 0 0 1-1.5 1.5A10 10 0 0 1 6.5 7.5 1.5 1.5 0 0 1 8 6z" fill="#0f4f8a"/></svg>
    123 456 7890
  </div>
</header>

<section class="hero">
  <div class="hero-art" role="img" aria-label="White silhouette of a family standing beneath an umbrella"></div>
  <h1 class="hero-title">Lorem ipsum dolor sit amet, consectetuer adipiscing elit sed diam</h1>
  <a class="btn">Get a Quote!</a>
</section>

<section class="quote-card">
  <div class="agent">
    <div class="agent-photo" role="img" aria-label="Portrait photo of the insurance agent"></div>
    <div class="agent-name">Dana Whitfield</div>
    <p class="contact">✆ 123 456 7890</p>
    <p class="contact">✉ hello@harborquote.com</p>
    <p>Lorem ipsum dolor sit amet, consec tetuer adipiscing elit sed diam nonummy nibh euismod tincidunt</p>
  </div>
  <div class="form">
    <h2>Get An Instant <b>Insurance Quote.</b></h2>
    <div class="fields">
      <div class="field"><label>Full Name:</label><span></span></div>
      <div class="field"><label>Street Address:</label><span></span></div>
      <div class="field"><label>Sex:</label><span>Select</span></div>
      <div class="field"><label>City:</label><span></span></div>
      <div class="field"><label>Date of Birth:</label><span>Month · Day · Year</span></div>
      <div class="field"><label>Zip Code:</label><span></span></div>
      <div class="field"><label>Current Health:</label><span>Select</span></div>
      <div class="field"><label>Phone:</label><span></span></div>
      <div class="field"><label>Coverage:</label><span>Select</span></div>
      <div class="field"><label>Email:</label><span></span></div>
    </div>
    <a class="btn submit">Submit</a>
  </div>
</section>

<section class="about">
  <h3>About <b>Insurance Agent</b></h3>
  <p>Lorem ipsum dolor sit amet, consectetuer adipiscing elit, sed diam nonummy nibh euismod tincidunt ut laoreet dolore magna aliquam erat volutpat. Ut wisi enim ad minim veniam, quis nostrud exerci tation ullamcorper suscipit lobortis nisl ut aliquip ex ea commodo consequat. Duis autem vel eum iriure dolor in hendrerit in vulputate velit esse molestie consequat, vel illum dolore eu feugiat nulla facilisis at vero eros et accumsan et iusto odio dignissim qui blandit praesent luptatum zzril delenit augue duis dolore te feugait nulla facilisi.</p>
</section>

<section class="products">
  <h3>Our <b>Insurance Products</b></h3>
  <div class="rule"></div>
  <div class="grid">
    <div class="product">
      <div class="hexicon"><svg width="30" height="28" viewBox="0 0 30 28"><path d="M15 26 3 14a6 6 0 0 1 12-8 6 6 0 0 1 12 8z" fill="#fff"/></svg></div>
      <h4>Life</h4>
      <p>Lorem ipsum dolor sit amet, consectetuer adipiscing elit, sed diam nonummy nibh euismod tincidunt.</p>
      <a class="btn">Get a Quote!</a>
    </div>
    <div class="product">
      <div class="hexicon"><svg width="34" height="22" viewBox="0 0 34 22"><path d="M3 12l4-8h20l4 8v6H3z" fill="#fff"/><circle cx="9" cy="18" r="3" fill="#2b2b2b" stroke="#fff" stroke-width="2"/><circle cx="25" cy="18" r="3" fill="#2b2b2b" stroke="#fff" stroke-width="2"/><path d="M9 6h16l2 5H7z" fill="#2b2b2b"/></svg></div>
      <h4>Auto</h4>
      <p>Lorem ipsum dolor sit amet, consectetuer adipiscing elit, sed diam nonummy nibh euismod tincidunt.</p>
      <a class="btn">Get a Quote!</a>
    </div>
    <div class="product">
      <div class="hexicon"><svg width="30" height="28" viewBox="0 0 30 28"><path d="M15 2 2 14h4v12h7v-8h4v8h7V14h4z" fill="#fff"/></svg></div>
      <h4>Home</h4>
      <p>Lorem ipsum dolor sit amet, consectetuer adipiscing elit, sed diam nonummy nibh euismod tincidunt.</p>
      <a class="btn">Get a Quote!</a>
    </div>
    <div class="product">
      <div class="hexicon"><svg width="30" height="26" viewBox="0 0 30 26"><rect x="2" y="7" width="26" height="17" rx="2" fill="#fff"/><path d="M10 7V3h10v4" fill="none" stroke="#fff" stroke-width="2.5"/><rect x="13" y="13" width="4" height="4" fill="#2b2b2b"/></svg></div>
      <h4>Business</h4>
      <p>Lorem ipsum dolor sit amet, consectetuer adipiscing elit, sed diam nonummy nibh euismod tincidunt.</p>
      <a class="btn">Get a Quote!</a>
    </div>
  </div>
</section>

<section class="testimonials">
  <h3>Client <b>Testimonials</b></h3>
  <div class="rule" style="margin-bottom:8px"></div>
  <svg class="arrow" style="left:24px" width="12" height="24" viewBox="0 0 12 24"><path d="M10 2 2 12l8 10" fill="none" stroke="#999" stroke-width="2"/></svg>
  <svg class="arrow" style="right:24px" width="12" height="24" viewBox="0 0 12 24"><path d="M2 2l8 10-8 10" fill="none" stroke="#999" stroke-width="2"/></svg>
  <div class="faces">
    <div class="face side" role="img" aria-label="Client portrait photo"></div>
    <div class="face main" role="img" aria-label="Featured client portrait photo"></div>
    <div class="face side" role="img" aria-label="Client portrait photo"></div>
  </div>
  <div class="t-name">Lorem ipsum dolor sit</div>
  <p>Lorem ipsum dolor sit amet, consectetuer adipiscing elit, sed diam<br>nonummy nibh euismod tincidunt ut laoreet dolore magna.</p>
</section>

<footer class="footer">
  <h5>Disclaimer:</h5>
  <p>Lorem ipsum dolor sit amet, consectetuer adipiscing elit, sed diam nonummy nibh euismod tincidunt ut laoreet dolore magna aliquam erat volutpat. Ut wisi enim ad minim veniam, quis nostrud exerci tation ullamcorper suscipit lobortis nisl ut aliquip ex ea commodo consequat.</p>
  <p class="copy">Copyright 2015 Harbor Quote &nbsp;|&nbsp; All rights reserved.</p>
</footer>
</body>
</html>
```